EB-5 Regional Center needs a Web design

Harlow Ridge Financial Partners is an expanding EB-r regional center. We have been successful in sponsoring multiple projects of third-party developers and placing EB-5, B-1, and Private Investments into multiple projects.

We are now partnering directly with project developers in the energy and healthcare to raise foreign capital for projects in those industries. The foreign capital is used as project equity and our collective balance sheets are used to guarantee debt to complete the funding of the projects.

We need a web site where we can post our company credentials, the bios of each partner, a document page for each of our projects where we can post specific project related documents which foreign investors can read, and we will need a section where foreign investors can fill out investor forms confirming that they are qualified investors and leaving their contact so that our agents and executives can make contact.

The final design should reflect the exceptional experience of the partners and our financial strength and stability.

We do have a logo we would want to use on the web design.

Target Market(s)

EB-5 Investors, B-1 Investors, Private Equity and other investors seeking quality investment in job creating US projects.

Coding

Number of Pages Required

5+ page

Font styles to use
Sans Serif

Requirements
Must have
• Pages to display company info, partner bios, projects completed, and a projects in-process page where we can post documents and info on projects for which we are seeking foreign investment. We also need a section where investors can enter their qualifying personal information and leave contact information for us.

```html
<!DOCTYPE html>
<html lang="en">
<head>
<meta charset="utf-8">
<title>Harlow Ridge Financial Partners</title>
<link href="https://fonts.googleapis.com/css2?family=Poppins:ital,wght@0,300;0,400;0,500;0,600;0,700;1,400&display=swap" rel="stylesheet">
<style>
:root{
  --ink:#1f1f1f;
  --text:#444;
  --muted:#6b6b6b;
  --white:#fff;
  --grey:#7b7b7b;
  --panel:#7d7d7d;
  --footer:#1d1d1f;
  --shadow:0 2px 10px rgba(0,0,0,.12);
}
*{box-sizing:border-box;margin:0;padding:0}
html,body{width:1200px;height:4152px;overflow:hidden;background:#fff}
body{font-family:'Poppins',sans-serif;color:var(--ink);position:relative}
.abs{position:absolute}

/* header + hero */
.hero{left:0;top:0;width:1200px;height:685px;background:linear-gradient(120deg,#55575b 0%,#3b3c40 55%,#2e2f33 100%)}
.topbar{left:111px;top:24px;width:978px;height:74px;background:var(--white);display:flex;align-items:center;padding:0 28px}
.brand{display:flex;align-items:center;gap:12px;font-weight:600;font-size:19px;color:#6d6d6d}
.brand-mark{width:30px;height:30px;background:#8a8a8a}
.nav{margin-left:auto;display:flex;gap:22px;font-size:14px;font-weight:500;color:#333}
.nav .active{border-bottom:2px solid #999}
.hero-name{left:111px;top:222px;color:var(--white);font-weight:600}
.hero-name .l1{font-size:84px;line-height:1;letter-spacing:1px;display:block}
.hero-name .l2{font-size:31px;letter-spacing:8px;display:block;margin-top:14px;font-weight:400}
.hero-copy{left:111px;top:384px;width:500px;color:var(--white);font-size:19px;line-height:32px}
.btn-outline{left:111px;top:478px;width:123px;height:58px;border:2px solid var(--white);color:var(--white);font-size:18px;display:flex;align-items:center;justify-content:center;font-weight:500}
.hero-visual{left:689px;top:185px;width:400px;height:430px}

/* section heads */
.kicker{font-size:17px;color:var(--muted);font-weight:300;line-height:1}
.sec-title{font-size:42px;font-weight:500;color:#8a8a8a;line-height:1.1}
.head{display:flex;gap:14px;align-items:center}
.head-mark{width:48px;height:48px;background:#9a9a9a;flex:none}
.body-copy{font-size:13px;line-height:22px;color:var(--text);text-align:justify}

/* services */
.svc-card{width:261px;height:256px;background:var(--white);box-shadow:var(--shadow);text-align:center;padding-top:20px}
.svc-card svg{width:52px;height:52px}
.svc-card h3{font-size:20px;font-weight:500;margin-top:14px}
.svc-card p{font-size:13px;line-height:22px;color:var(--text);padding:8px 14px 0}
.svc-card .more{font-size:14px;font-weight:500;margin-top:18px;display:block}
.svc-photo{left:696px;top:764px;width:393px;height:721px;background:linear-gradient(160deg,#8e8f92,#4d4e52 60%,#2f3034)}

/* projects */
.band{left:0;top:1579px;width:1200px;height:478px;background:linear-gradient(100deg,#2c2d30,#4a4b4f 50%,#2b2c2f)}
.band-copy{left:111px;top:1646px;width:612px;color:var(--white);font-size:13px;line-height:22px;text-align:justify}
.band-head{left:757px;top:1656px;color:var(--white);text-align:right}
.band-head .kicker{color:#ddd}
.band-head .sec-title{color:var(--white)}
.proj{width:311px;height:409px;background:var(--white);padding:8px;box-shadow:var(--shadow)}
.proj-img{width:295px;height:276px}
.proj-cap{width:295px;height:116px;margin-top:9px;background:#000;color:var(--white);padding:26px 20px}
.proj-cap.alt{background:var(--grey)}
.proj-cap h4{font-size:22px;font-weight:500}
.proj-cap span{font-size:14px}
.arrow{top:1895px}

/* partners */
.bio{width:231px;height:339px;background:var(--white);box-shadow:var(--shadow);padding:9px;text-align:center}
.bio-img{width:213px;height:238px}
.bio h5{font-size:20px;font-weight:500;margin-top:22px;line-height:1}
.bio span{font-size:15px;color:#444}
.bio-over{position:absolute;left:9px;top:9px;width:213px;height:321px;background:#4a4a4c;color:var(--white);padding:18px 14px 0}
.bio-over h5{margin-top:0;font-size:20px}
.bio-over span{color:var(--white);display:block;margin-top:6px}
.bio-over p{font-size:13px;line-height:22px;margin-top:14px}
.socials{display:flex;gap:10px;justify-content:center;margin-top:10px}
.dot{width:18px;height:18px;border-radius:50%;background:var(--white)}

/* contact */
.contact-photo{left:0;top:2839px;width:599px;height:588px;background:linear-gradient(150deg,#6a6b6e,#3a3b3f 60%,#27282b)}
.contact-panel{left:599px;top:2839px;width:601px;height:588px;background:var(--panel)}
.field{left:625px;width:464px;height:58px;border:2px solid var(--white);color:var(--white);font-size:17px;padding:0 12px;display:flex;align-items:center}
.note{left:625px;top:3272px;font-size:15px;font-style:italic;color:var(--white)}
.btn-solid{left:625px;top:3314px;width:132px;height:58px;background:var(--white);color:#222;font-size:17px;font-weight:500;display:flex;align-items:center;justify-content:center}

/* partner badges */
.badge{top:3504px;width:177px;height:96px;background:var(--white);box-shadow:0 1px 8px rgba(0,0,0,.08);display:flex;align-items:center;justify-content:center}
.badge i{width:80px;height:40px;background:#9a9a9a;display:block;border-radius:4px}

/* footer */
.footer{left:0;top:3670px;width:1200px;height:482px;background:var(--footer);color:var(--white)}
.f-brand{left:101px;top:3772px;width:280px;text-align:center;font-weight:600;font-size:22px;line-height:28px;color:var(--white)}
.f-brand .mark{width:56px;height:56px;background:#9a9a9a;margin:0 auto 16px}
.f-social{left:111px;top:3934px;display:flex;gap:13px}
.f-social i{width:40px;height:40px;border:2px solid var(--white);border-radius:50%;display:block}
.f-title{font-size:23px;font-weight:500}
.links{list-style:none;margin-top:14px;font-size:15px;font-weight:500}
.links li{height:29px}
.links li::before{content:"»";margin-right:14px}
.c-row{display:flex;align-items:center;gap:16px;font-size:14px;font-weight:500;line-height:21px}
.c-ico{width:48px;height:48px;border:2px solid var(--white);border-radius:50%;display:flex;align-items:center;justify-content:center;flex:none}
.rule{left:111px;top:4063px;width:978px;height:1px;background:#555}
.copyright{left:0;top:4092px;width:1200px;text-align:center;font-size:15px;font-weight:500;color:var(--white)}
</style>
</head>
<body>

<!-- hero -->
<div class="abs hero" role="img" aria-label="Business meeting with charts and a pen on a desk"></div>
<header class="abs topbar">
  <div class="brand"><span class="brand-mark"></span>Harlow Ridge Financial Partners</div>
  <nav class="nav"><span class="active">HOME</span><span>PAGES</span><span>NEWS</span><span>PROJECTS</span><span>SERVICES</span><span>SHOP</span><span>CONTACT</span></nav>
</header>
<h1 class="abs hero-name"><span class="l1">HARLOW RIDGE</span><span class="l2">Financial Partners</span></h1>
<p class="abs hero-copy">Duis aute irure dolor in reprehenderit in voluptate velit esse cillum dolorem.</p>
<a class="abs btn-outline">Read More</a>
<svg class="abs hero-visual" viewBox="0 0 400 430" role="img" aria-label="Man writing at a desk framed in a diamond">
  <defs><linearGradient id="dg" x1="0" y1="0" x2="0" y2="1"><stop offset="0" stop-color="#d6d7d9"/><stop offset="1" stop-color="#8d8e91"/></linearGradient></defs>
  <polygon points="200,0 400,215 200,430 0,215" fill="url(#dg)"/>
</svg>

<!-- services -->
<div class="abs head" style="left:111px;top:764px">
  <span class="head-mark"></span>
  <div><div class="kicker">Harlow Ridge</div><div class="sec-title">Our Services</div></div>
</div>
<p class="abs body-copy" style="left:111px;top:850px;width:545px">Harlow Ridge Financial Partners is an expanding EB-r regional center. We have been successful in sponsoring multiple projects of third-party developers and placing EB-5, B-1, and Private Investments into multiple projects.</p>

<div class="abs svc-card" style="left:111px;top:947px">
  <svg viewBox="0 0 52 52" fill="none" stroke="#222" stroke-width="2"><rect x="6" y="34" width="6" height="12"/><rect x="16" y="28" width="6" height="18"/><rect x="26" y="22" width="6" height="24"/><polyline points="6,26 18,18 28,20 44,6"/><circle cx="42" cy="40" r="7"/></svg>
  <h3>General Accounting</h3>
  <p>Lorem ipsum dolor sit amet, consectetur adipiscing elit. Pellent esque dignissim.</p>
  <span class="more">Read More »</span>
</div>
<div class="abs svc-card" style="left:395px;top:947px">
  <svg viewBox="0 0 52 52" fill="none" stroke="#222" stroke-width="2"><circle cx="26" cy="18" r="9"/><path d="M6 36h10l8 4h12l10-6M6 44h14l10 2h8"/><path d="M4 18h8M40 18h8"/></svg>
  <h3>Foreign Investors</h3>
  <p>Lorem ipsum dolor sit amet, consectetur adipiscing elit. Pellent esque dignissim.</p>
  <span class="more">Read More »</span>
</div>
<div class="abs svc-card" style="left:111px;top:1229px">
  <svg viewBox="0 0 52 52" fill="none" stroke="#222" stroke-width="2"><circle cx="26" cy="26" r="11"/><path d="M26 4v8M26 40v8M4 26h8M40 26h8M10 10l6 6M36 36l6 6M42 10l-6 6M16 36l-6 6"/></svg>
  <h3>Capital Investments</h3>
  <p>Lorem ipsum dolor sit amet, consectetur adipiscing elit. Pellent esque dignissim.</p>
  <span class="more">Read More »</span>
</div>
<div class="abs svc-card" style="left:395px;top:1229px">
  <svg viewBox="0 0 52 52" fill="none" stroke="#222" stroke-width="2"><rect x="8" y="32" width="6" height="14"/><rect x="18" y="26" width="6" height="20"/><rect x="28" y="30" width="6" height="16"/><rect x="38" y="18" width="6" height="28"/><polyline points="8,24 20,16 30,22 44,6"/></svg>
  <h3>Financial Services</h3>
  <p>Lorem ipsum dolor sit amet, consectetur adipiscing elit. Pellent esque dignissim.</p>
  <span class="more">Read More »</span>
</div>
<div class="abs svc-photo" role="img" aria-label="Smiling businesswoman in a dark blazer"></div>

<!-- projects -->
<div class="abs band" role="img" aria-label="Dimmed office background"></div>
<p class="abs band-copy">Harlow Ridge Financial Partners is an expanding EB-r regional center. We have been successful in sponsoring multiple projects of third-party developers and placing EB-5, B-1, and Private Investments into multiple projects.</p>
<div class="abs band-head head">
  <div><div class="kicker">Harlow Ridge</div><div class="sec-title">Our Projects</div></div>
  <span class="head-mark" style="background:#d0d0d0"></span>
</div>
<svg class="abs arrow" style="left:32px" width="26" height="50" viewBox="0 0 26 50"><polyline points="24,2 2,25 24,48" fill="none" stroke="#fff" stroke-width="3"/></svg>
<svg class="abs arrow" style="left:1132px" width="26" height="50" viewBox="0 0 26 50"><polyline points="2,2 24,25 2,48" fill="none" stroke="#fff" stroke-width="3"/></svg>

<div class="abs proj" style="left:111px;top:1779px">
  <div class="proj-img" style="background:linear-gradient(135deg,#d9d4cc,#9a8f84)" role="img" aria-label="Team reviewing a tablet at a table"></div>
  <div class="proj-cap"><h4>Duis Aute Irure</h4><span>Nemo enim ipsam</span></div>
</div>
<div class="abs proj" style="left:445px;top:1779px">
  <div class="proj-img" style="background:linear-gradient(135deg,#c9d3dc,#6f7e8c)" role="img" aria-label="Hands pointing at printed financial charts"></div>
  <div class="proj-cap alt"><h4>Duis Aute Irure</h4><span>Nemo enim ipsam</span></div>
</div>
<div class="abs proj" style="left:778px;top:1779px">
  <div class="proj-img" style="background:linear-gradient(135deg,#8a8f97,#2d3440)" role="img" aria-label="Businessman holding a tablet with charts"></div>
  <div class="proj-cap"><h4>Duis Aute Irure</h4><span>Nemo enim ipsam</span></div>
</div>

<!-- partners -->
<div class="abs head" style="left:111px;top:2276px">
  <span class="head-mark"></span>
  <div><div class="kicker">Harlow Ridge</div><div class="sec-title">Partner Bios</div></div>
</div>
<p class="abs body-copy" style="left:468px;top:2272px;width:621px">Harlow Ridge Financial Partners is an expanding EB-r regional center. We have been successful in sponsoring multiple projects of third-party developers and placing EB-5, B-1, and Private Investments into multiple projects.</p>

<div class="abs bio" style="left:111px;top:2395px">
  <div class="bio-img" style="background:linear-gradient(#e3e3e3,#bdbdbd)" role="img" aria-label="Portrait of a partner in a dark suit"></div>
  <h5>Evan Marlow</h5><span>Management Team</span>
</div>
<div class="abs bio" style="left:361px;top:2395px">
  <div class="bio-over">
    <h5>Clara Denholm</h5><span>Management Team</span>
    <p>Nemo enim ipsam voluptatem quia voluptas sit aspernatur aut odit aut fugit, sed quia consequuntur magni dolores eos qui ratione voluptatem.</p>
    <div class="socials"><i class="dot"></i><i class="dot"></i><i class="dot"></i></div>
  </div>
</div>
<div class="abs bio" style="left:611px;top:2395px">
  <div class="bio-img" style="background:linear-gradient(#e3e3e3,#bdbdbd)" role="img" aria-label="Portrait of a partner in a dark jacket"></div>
  <h5>Rafael Ortiz</h5><span>Management Team</span>
</div>
<div class="abs bio" style="left:860px;top:2395px">
  <div class="bio-img" style="background:linear-gradient(#e3e3e3,#c4bfb8)" role="img" aria-label="Portrait of a partner in a light blazer"></div>
  <h5>Nina Calloway</h5><span>Management Team</span>
</div>

<!-- contact -->
<div class="abs contact-photo" role="img" aria-label="Man in glasses working at a desk, video thumbnail"></div>
<svg class="abs" style="left:242px;top:3076px" width="114" height="114" viewBox="0 0 114 114"><circle cx="57" cy="57" r="53" fill="none" stroke="#fff" stroke-width="5"/><polygon points="44,34 82,57 44,80" fill="#fff"/></svg>
<div class="abs contact-panel"></div>
<div class="abs head" style="left:627px;top:2890px;color:#fff">
  <span class="head-mark" style="background:#d6d6d6;width:56px;height:56px"></span>
  <div><div class="kicker" style="color:#eee">Harlow Ridge</div><div class="sec-title" style="color:#fff">Contact Form</div></div>
</div>
<div class="abs field" style="top:2993px">Name</div>
<div class="abs field" style="top:3062px">Email</div>
<div class="abs field" style="top:3130px">Phone Number</div>
<div class="abs field" style="top:3199px">Services Required</div>
<p class="abs note">**Contact our support team if you have any questions.</p>
<a class="abs btn-solid">Submit Now</a>

<!-- partner badges -->
<div class="abs badge" style="left:111px"><i></i></div>
<div class="abs badge" style="left:311px"><i></i></div>
<div class="abs badge" style="left:511px"><i></i></div>
<div class="abs badge" style="left:711px"><i></i></div>
<div class="abs badge" style="left:911px"><i></i></div>

<!-- footer -->
<footer class="abs footer"></footer>
<div class="abs f-brand"><div class="mark"></div>Harlow Ridge<br>Financial Partners</div>
<div class="abs f-social"><i></i><i></i><i></i><i></i><i></i></div>
<div class="abs" style="left:480px;top:3748px;color:#fff">
  <div class="f-title">Quick Links</div>
  <ul class="links"><li>HOME</li><li>PAGES</li><li>NEWS</li><li>PROJECTS</li><li>SERVICES</li><li>SHOP</li><li>CONTACT</li></ul>
</div>
<div class="abs" style="left:710px;top:3748px;color:#fff">
  <div class="f-title">Contact Us</div>
  <div class="c-row" style="margin-top:24px">
    <span class="c-ico"><svg width="22" height="22" viewBox="0 0 22 22" fill="none" stroke="#fff" stroke-width="2"><path d="M11 20s7-7 7-12a7 7 0 0 0-14 0c0 5 7 12 7 12z"/><circle cx="11" cy="8" r="2.5"/></svg></span>
    <span>Nemo enim ipsam voluptatem quia<br>voluptas sit aspernatur aut odit</span>
  </div>
  <div class="c-row" style="margin-top:22px">
    <span class="c-ico"><svg width="22" height="22" viewBox="0 0 22 22" fill="none" stroke="#fff" stroke-width="2"><path d="M5 2l4 4-2 3c1 3 3 5 6 6l3-2 4 4-3 3C9 20 2 13 2 5z"/></svg></span>
    <span>Phone: +1 555 014 2287</span>
  </div>
  <div class="c-row" style="margin-top:22px">
    <span class="c-ico"><svg width="22" height="18" viewBox="0 0 22 18" fill="none" stroke="#fff" stroke-width="2"><rect x="1" y="1" width="20" height="16"/><polyline points="1,1 11,10 21,1"/></svg></span>
    <span>info@harlowridgefinancial.com</span>
  </div>
</div>
<div class="abs rule"></div>
<p class="abs copyright">Copyrights @ 2020 Harlow Ridge Financial Partners. All Rights Reserved.</p>

</body>
</html>
```